Candle Rental Business seeks new website design

We need a new website design for a Candle hire business. The business rents out pillar candles for events such as weddings and corporate events. Our main target market is weddings. The business name is Hire a Lantern. The business name does not have a logo design.

We would like a website that is light in colours and creates a warm atmosphere. The design needs to be elegant and upmarket. There are different size candles that we hire out, ranging from 10cm diameter to 20cm diameter, flat, tall etc. All our candles are white in colour. Its just the size that differs.

We would also like to include a section for hiring out decor such as glassvases, candlebras, overlays and chairs sachets, chair covers. However, this is not the businesses main focus but an additional offering to customers.

Target Market(s)

Wedding venues and brides. Corporate events. School dances.

Industry/Entity Type

Hospitality

Logo Text

Hire a Lantern

Number of Pages Required

1 page

Font styles to use
Sans Serif
Script

Requirements
Must have
• Pictures of pillar candles. Plain white candles. The website must centre around candles.
Nice to have
• Different examples of candle centrepieces
Should not have
• Pictures must not be of brides. Pictures of surrounding is perferable.

```html
<!DOCTYPE html>
<html lang="en">
<head>
<meta charset="utf-8">
<title>Hire a Lantern – Candle Hire</title>
<link href="https://fonts.googleapis.com/css2?family=Great+Vibes&family=Open+Sans:wght@400;600;700&display=swap" rel="stylesheet">
<style>
:root{
  --green:#5a9127;
  --green-dark:#467520;
  --green-tint:#eef5e6;
  --ink:#333333;
  --muted:#6b6b6b;
  --rule:#dcdcdc;
  --white:#ffffff;
  --footer:#2a2a2a;
  --footer-base:#1c1c1c;
  --footer-text:#c9c9c9;
}
*{box-sizing:border-box;margin:0;padding:0}
html,body{width:1200px;height:2528px;overflow:hidden}
body{font-family:"Open Sans",Arial,sans-serif;color:var(--ink);background:var(--white);position:relative}
.script{font-family:"Great Vibes",cursive;font-weight:400}

/* header */
.site-header{position:absolute;top:0;left:0;width:1200px;height:88px;background:var(--white);border-bottom:1px solid var(--rule)}
.brand{position:absolute;left:60px;top:22px;display:flex;align-items:center;gap:10px}
.brand-dot{width:14px;height:14px;border-radius:50%;background:var(--green)}
.brand-name{font-family:"Great Vibes",cursive;font-size:38px;color:var(--green-dark);line-height:1}
.topbar{position:absolute;right:60px;top:10px;font-size:12px;color:var(--muted);display:flex;gap:22px}
.topbar span{display:flex;align-items:center;gap:6px}
.main-nav{position:absolute;right:60px;top:44px;display:flex;gap:4px}
.main-nav a{font-size:13px;color:var(--ink);text-decoration:none;padding:10px 16px;font-weight:600}
.main-nav a.active{background:var(--green-tint);color:var(--green-dark);border-bottom:2px solid var(--green)}

/* hero */
.hero{position:absolute;top:88px;left:0;width:1200px;height:512px;
  background:radial-gradient(ellipse at 35% 40%,#e9e3ee 0%,#a49ab8 30%,#4b4366 62%,#22203a 100%)}
.hero-title{position:absolute;left:0;right:0;top:232px;text-align:center;font-size:48px;color:var(--white);text-shadow:0 2px 6px rgba(0,0,0,.45)}

/* section headings */
.section-title{position:absolute;left:0;width:1200px;text-align:center;font-size:42px;color:var(--ink);line-height:1}
.section-title .accent{color:var(--green)}
.title-rule{position:absolute;left:530px;width:140px;height:14px}

/* about */
.about-text{position:absolute;left:160px;top:718px;width:880px;text-align:center;font-size:13px;line-height:22px;color:var(--muted)}

/* services */
.services{position:absolute;top:832px;left:0;width:1200px;height:548px;background:var(--green-tint)}
.service-card{position:absolute;top:148px;width:340px;height:340px;background:var(--white);box-shadow:0 1px 3px rgba(0,0,0,.12)}
.service-card h3{height:58px;background:var(--green);color:var(--white);font-size:20px;font-weight:600;padding:16px 14px}
.service-photo{height:140px;margin:8px 0 0}
.service-card p{font-size:12.5px;line-height:19px;padding:12px 50px 0 14px;color:var(--ink)}
.more-btn{position:absolute;right:12px;bottom:16px;width:32px;height:32px;background:#3a3a3a;display:flex;align-items:center;justify-content:center}

/* products */
.product-tile{position:absolute}
.zoom{position:absolute;left:50%;top:48px;margin-left:-20px;width:40px;height:40px;border-radius:50%;background:var(--green);display:flex;align-items:center;justify-content:center}
.tile-caption{position:absolute;left:0;right:0;top:104px;text-align:center;font-size:12px;color:var(--white)}

/* testimonial */
.avatar{position:absolute;left:60px;top:2028px;width:112px;height:112px;border-radius:50%;background:radial-gradient(circle at 50% 40%,#efe7df,#b9aa9c);border:4px solid var(--white);box-shadow:0 0 0 2px var(--green)}
.quote{position:absolute;left:200px;top:2036px;width:940px;font-size:13px;line-height:22px;color:var(--muted);font-style:italic}
.quote-author{position:absolute;left:200px;top:2120px;font-size:13px;font-weight:700;color:var(--ink)}

/* footer */
.site-footer{position:absolute;top:2220px;left:0;width:1200px;height:268px;background:var(--footer);border-top:4px solid var(--green);color:var(--footer-text)}
.footer-col{position:absolute;top:28px}
.footer-col h4{font-size:15px;color:var(--white);font-weight:600;margin-bottom:16px}
.footer-links{list-style:none;font-size:12.5px;line-height:24px}
.footer-links li::before{content:"›";color:var(--green);margin-right:8px}
.contact-line{display:flex;align-items:center;gap:10px;font-size:12.5px;margin-bottom:16px}
.contact-icon{width:28px;height:28px;border-radius:50%;background:var(--green);display:flex;align-items:center;justify-content:center;flex:none}
.field{width:230px;height:28px;background:var(--white);margin-bottom:8px;font-size:11px;color:#888;padding:6px 8px}
.field.tall{height:56px}
.submit{display:inline-block;background:var(--green);color:var(--white);font-size:12px;padding:6px 16px}
.footer-brand{position:absolute;left:900px;top:70px;display:flex;align-items:center;gap:10px}
.footer-brand .brand-name{color:var(--white);font-size:40px}
.follow{position:absolute;left:880px;top:218px;display:flex;align-items:center;gap:8px;font-size:12px}
.social{width:24px;height:24px;border-radius:50%;background:var(--white)}
.footer-base{position:absolute;top:2488px;left:0;width:1200px;height:40px;background:var(--footer-base);color:#9a9a9a;font-size:11.5px;padding:13px 60px}
</style>
</head>
<body>

<header class="site-header">
  <div class="brand"><span class="brand-dot"></span><span class="brand-name">Hire a Lantern</span></div>
  <div class="topbar">
    <span><svg width="12" height="12" viewBox="0 0 24 24"><path fill="#5a9127" d="M6.6 10.8a15 15 0 0 0 6.6 6.6l2.2-2.2c.3-.3.7-.4 1-.2 1.1.4 2.3.6 3.6.6.6 0 1 .4 1 1V20c0 .6-.4 1-1 1A17 17 0 0 1 3 4c0-.6.4-1 1-1h3.5c.6 0 1 .4 1 1 0 1.3.2 2.5.6 3.6.1.3 0 .7-.2 1z"/></svg>(0800) 555 0142</span>
    <span><svg width="13" height="10" viewBox="0 0 26 20"><rect x="1" y="1" width="24" height="18" fill="none" stroke="#5a9127" stroke-width="2"/><path d="M1 1l12 10L25 1" fill="none" stroke="#5a9127" stroke-width="2"/></svg>hello@hirealantern.com</span>
  </div>
  <nav class="main-nav">
    <a class="active">Home</a><a>About Us</a><a>Weddings</a><a>Corporate events</a><a>For Hire</a><a>Contact</a>
  </nav>
</header>

<section class="hero" role="img" aria-label="Candlelit banquet hall with glass cylinder candle centrepieces">
  <h1 class="hero-title script">Meaningful gift at a friendly price point</h1>
</section>

<h2 class="section-title" style="top:640px"><span style="font-weight:700;font-family:'Open Sans',sans-serif;font-size:30px">About </span><span class="script accent">Hire a Lantern</span></h2>
<svg class="title-rule" style="top:690px" viewBox="0 0 140 14"><line x1="0" y1="7" x2="58" y2="7" stroke="#5a9127"/><circle cx="70" cy="7" r="4" fill="#5a9127"/><line x1="82" y1="7" x2="140" y2="7" stroke="#5a9127"/></svg>
<p class="about-text">We are a family owned and operated business that began by lighting rooms for every kind of celebration. All of our candles are plain white pillars, chosen for a clean and timeless look, and stored with care in our workshop. Our aim is to provide a warm glow at a fair price, with pieces that have been tested for long and steady burning. Explore our products.</p>

<section class="services">
  <h2 class="section-title script" style="top:60px">Our <span class="accent">Services</span></h2>
  <svg class="title-rule" style="top:110px" viewBox="0 0 140 14"><line x1="0" y1="7" x2="58" y2="7" stroke="#5a9127"/><circle cx="70" cy="7" r="4" fill="#5a9127"/><line x1="82" y1="7" x2="140" y2="7" stroke="#5a9127"/></svg>

  <article class="service-card" style="left:60px">
    <h3>Hire Candles</h3>
    <div class="service-photo" role="img" aria-label="White pillar candles in glass holders on a reception table" style="background:linear-gradient(135deg,#3b3a36,#a89c82 55%,#e8dfc9)"></div>
    <p>Do you love using candles for your events but tired of seeing old used candles or buying expensive candles?</p>
    <span class="more-btn"><svg width="10" height="14" viewBox="0 0 10 14"><path d="M2 1l6 6-6 6" fill="none" stroke="#fff" stroke-width="2"/></svg></span>
  </article>

  <article class="service-card" style="left:430px">
    <h3>Personalized Candles</h3>
    <div class="service-photo" role="img" aria-label="Candle centrepiece with flowers on a dark table" style="background:linear-gradient(135deg,#1b2a17,#4d5b34 50%,#d8cfae)"></div>
    <p>Hire a Lantern provides the opportunity to give a thoughtful, meaningful gift at a friendly price point. This gives you</p>
    <span class="more-btn"><svg width="10" height="14" viewBox="0 0 10 14"><path d="M2 1l6 6-6 6" fill="none" stroke="#fff" stroke-width="2"/></svg></span>
  </article>

  <article class="service-card" style="left:800px">
    <h3>Decor Hire</h3>
    <div class="service-photo" role="img" aria-label="Event room with chair covers and pink uplighting" style="background:linear-gradient(135deg,#5b2a5e,#c766b8 50%,#f3d5ee)"></div>
    <p>We hire a selection of overlays, chair sashes and chair covers as well as glassware and candelabras to compliment</p>
    <span class="more-btn"><svg width="10" height="14" viewBox="0 0 10 14"><path d="M2 1l6 6-6 6" fill="none" stroke="#fff" stroke-width="2"/></svg></span>
  </article>
</section>

<h2 class="section-title script" style="top:1412px">Our <span class="accent">Products</span></h2>
<svg class="title-rule" style="top:1462px" viewBox="0 0 140 14"><line x1="0" y1="7" x2="58" y2="7" stroke="#5a9127"/><circle cx="70" cy="7" r="4" fill="#5a9127"/><line x1="82" y1="7" x2="140" y2="7" stroke="#5a9127"/></svg>

<div class="product-tile" role="img" aria-label="Group of white pillar candles of different heights" style="left:60px;top:1512px;width:388px;height:348px;background:linear-gradient(135deg,#f4ecd8,#d8c7a2 50%,#8e7c5c)"></div>
<div class="product-tile" role="img" aria-label="Candles on a dining table in a dim room" style="left:460px;top:1512px;width:400px;height:168px;background:linear-gradient(135deg,#2b2b2b,#5c554a 60%,#8a8070)">
  <span class="zoom"><svg width="18" height="18" viewBox="0 0 20 20"><circle cx="8" cy="8" r="6" fill="none" stroke="#fff" stroke-width="2"/><line x1="12.5" y1="12.5" x2="18" y2="18" stroke="#fff" stroke-width="2"/></svg></span>
  <span class="tile-caption">Lorem ipsum dolor sit amet</span>
</div>
<div class="product-tile" role="img" aria-label="Tall white candle in a glass vase" style="left:460px;top:1692px;width:194px;height:168px;background:linear-gradient(160deg,#1e1e1e,#6a6256 60%,#d9d0bd)"></div>
<div class="product-tile" role="img" aria-label="Pillar candles lit on a dark surface" style="left:666px;top:1692px;width:194px;height:168px;background:linear-gradient(160deg,#151515,#4d463c 55%,#c9bca0)"></div>
<div class="product-tile" role="img" aria-label="Floral centrepiece with white candles" style="left:872px;top:1512px;width:268px;height:348px;background:linear-gradient(135deg,#e4e8e0,#b9c4a8 50%,#7d8a6b)"></div>

<svg style="position:absolute;left:60px;top:1904px" width="1080" height="2"><line x1="0" y1="1" x2="1080" y2="1" stroke="#dcdcdc"/></svg>
<h2 class="section-title script" style="top:1940px">Client <span class="accent">Testimonial</span></h2>
<svg class="title-rule" style="top:1990px" viewBox="0 0 140 14"><line x1="0" y1="7" x2="58" y2="7" stroke="#5a9127"/><circle cx="70" cy="7" r="4" fill="#5a9127"/><line x1="82" y1="7" x2="140" y2="7" stroke="#5a9127"/></svg>

<div class="avatar" role="img" aria-label="Client portrait"></div>
<p class="quote">“The candles turned our reception into something truly magical. Every table glowed, the pillars looked fresh and clean, and the team set everything up before we arrived. Guests kept asking where the lighting came from, and the price was far better than buying new. We will gladly book again.”</p>
<p class="quote-author">– Miss Clara Whitfield</p>

<footer class="site-footer">
  <div class="footer-col" style="left:60px">
    <h4>Quick Link</h4>
    <ul class="footer-links"><li>Home</li><li>About Us</li><li>Weddings</li><li>Corporate Events</li><li>For Hire</li><li>Contact</li></ul>
  </div>
  <div class="footer-col" style="left:300px">
    <h4>Contact Information</h4>
    <div class="contact-line"><span class="contact-icon"><svg width="12" height="14" viewBox="0 0 12 16"><path d="M6 0a6 6 0 0 0-6 6c0 4.5 6 10 6 10s6-5.5 6-10a6 6 0 0 0-6-6zm0 8.2A2.2 2.2 0 1 1 6 3.8a2.2 2.2 0 0 1 0 4.4z" fill="#fff"/></svg></span><span>48 Willow Lane, Fernhill,<br>Auckland</span></div>
    <div class="contact-line"><span class="contact-icon"><svg width="12" height="12" viewBox="0 0 24 24"><path fill="#fff" d="M6.6 10.8a15 15 0 0 0 6.6 6.6l2.2-2.2c.3-.3.7-.4 1-.2 1.1.4 2.3.6 3.6.6.6 0 1 .4 1 1V20c0 .6-.4 1-1 1A17 17 0 0 1 3 4c0-.6.4-1 1-1h3.5c.6 0 1 .4 1 1 0 1.3.2 2.5.6 3.6.1.3 0 .7-.2 1z"/></svg></span><span style="font-size:17px;color:#fff">(0800) 555 0142</span></div>
    <div class="contact-line"><span class="contact-icon"><svg width="13" height="10" viewBox="0 0 26 20"><rect x="1" y="1" width="24" height="18" fill="none" stroke="#fff" stroke-width="2"/><path d="M1 1l12 10L25 1" fill="none" stroke="#fff" stroke-width="2"/></svg></span><span>hello@hirealantern.com</span></div>
  </div>
  <div class="footer-col" style="left:600px">
    <h4>Quick Inquiry</h4>
    <div class="field">Name</div>
    <div class="field">Email</div>
    <div class="field tall">Message</div>
    <span class="submit">Submit</span>
  </div>
  <div class="footer-brand"><span class="brand-dot"></span><span class="brand-name">Hire a Lantern</span></div>
  <div class="follow"><span>Follow us on</span><span class="social"></span><span class="social"></span><span class="social"></span><span class="social"></span></div>
</footer>
<div class="footer-base">Copyright © 2024 Hire a Lantern. All rights reserved.</div>

</body>
</html>
```